Business Card - high end, modern health care

Hey designers!

We need a double sided business card for the boutique, cutting edge physical therapy rehabilitation centre in Sydney's Northern Beaches.

With the most qualified physios in the area The Harbourview Motion Clinic does what other physiotherapy practices do not, we take our time with our patients giving them longer appointments, better physios and therefor faster results!

We guarantee that the service people receive at THMC will be unparalleled.

Hence we need a business card to reflect our modern, boutique, high end service. The final design needs to reflect that we are in a class of our own yet with the feel of beachside retreat.

Below I have attached our logo in both blue on white and white on blue. The exact colour is;
and the font that we have used in our logo is Tex Gyre Aventador.

I like the idea of the blue as the main colour as it is more eye catching and our signage onto the main road will be in this blue and in the interest of consistency across marketing the blue needs to be a part of the design. However I would appreciate a few designs onto a wooden background as this is a visual theme within the fitout of the practice.

The design needs to be of standard size (91x55mm).

Target Market(s)

We target people who have an end outcome in mind and those who have had poor experiences with other providers and ensure that everyone gets the care that they deserve with a premium service that is tailored to the individuals circumstances. As a premium service, the target market is highly educated, business and tech savvy with the additional target market of elderly people who have self funded their retirement and see value in paying for the best ongoing rehabilitation to maintain independence.

Industry/Entity Type

Physical Therapy

Contact Information for Business Card

Name, designation( Titled Musculoskeletal Physiotherapist... there will also be those in the company that have multiple designations ie 5 or 6 words long), phone number, email, facebook, instagram, address

Font styles to use
Sans Serif

Colors

Designer to choose colors to be used in the design.

Requirements
Must have
• Front - The logo as large as possible, blue or wooden theme, and all of the important details.
• Back - A blank space/lines on which to write appointment times (no "Appointment, date, time" etc.)
Nice to have
• facebook url
• logos for facebook and instagram
• Mini logos for the phone and email?

```html
<!DOCTYPE html>
<html lang="en">
<head>
<meta charset="utf-8">
<title>The Harbourview Motion Clinic – Business Card</title>
<link rel="stylesheet" href="https://fonts.googleapis.com/css2?family=Roboto:wght@400;700&family=Roboto+Condensed:wght@700&family=Source+Sans+3:wght@400&display=swap">
<style>
  :root {
    --backdrop: #1f1f1f;
    --card: #f4f4f4;
    --card-back: #ffffff;
    --brand-blue: #0057a8;
    --text-grey: #555555;
    --rule: #6a6a6a;
    --watermark: #eef2f8;
  }
  * { margin: 0; padding: 0; box-sizing: border-box; }
  html, body { width: 1200px; height: 960px; overflow: hidden; }
  body {
    position: relative;
    background: var(--backdrop);
    font-family: "Roboto", Arial, sans-serif;
  }
  .card {
    position: absolute;
    width: 600px;
    height: 342px;
    border-radius: 18px;
    overflow: hidden;
  }
  .card--front { left: 322px; top: 108px; background: var(--card); }
  .card--back  { left: 320px; top: 493px; background: var(--card-back); }

  /* Front */
  .name-band {
    position: absolute;
    left: 0; top: 34px;
    width: 344px; height: 45px;
    background: var(--brand-blue);
    color: #fff;
    padding: 5px 0 0 28px;
  }
  .name-band__name {
    font-family: "Roboto Condensed", "Arial Narrow", sans-serif;
    font-weight: 700;
    font-size: 21px;
    line-height: 22px;
    letter-spacing: 0.2px;
  }
  .name-band__title {
    font-family: "Roboto Condensed", "Arial Narrow", sans-serif;
    font-weight: 700;
    font-size: 14px;
    line-height: 15px;
  }
  .brand {
    position: absolute;
    left: 296px; top: 32px;
    display: flex;
    align-items: center;
    gap: 8px;
  }
  .brand__dot {
    width: 48px; height: 48px;
    border-radius: 50%;
    background: var(--brand-blue);
    border: 3px solid var(--card);
    flex: none;
  }
  .brand__name {
    color: var(--brand-blue);
    font-weight: 700;
    font-size: 19px;
    line-height: 21px;
    letter-spacing: 0.3px;
    text-transform: uppercase;
  }
  .contact-list {
    position: absolute;
    left: 30px; top: 232px;
    list-style: none;
    font-size: 14px;
    color: var(--text-grey);
  }
  .contact-list li {
    display: flex;
    align-items: center;
    height: 19px;
  }
  .contact-list svg, .contact-list .social-square {
    width: 13px; height: 13px;
    margin-right: 9px;
    flex: none;
  }
  .social-square { background: var(--brand-blue); border-radius: 1px; }
  .address {
    position: absolute;
    right: 29px; top: 256px;
    text-align: right;
    font-size: 14px;
    line-height: 19px;
    color: var(--text-grey);
    font-style: normal;
  }

  /* Back */
  .watermark {
    position: absolute;
    left: 151px; top: 23px;
    width: 298px; height: 298px;
    border-radius: 50%;
    background: var(--watermark);
  }
  .appointment {
    position: absolute;
    inset: 0;
    font-family: "Source Sans 3", "Myriad Pro", sans-serif;
    font-size: 16px;
    color: var(--text-grey);
  }
  .field {
    position: absolute;
    display: flex;
    align-items: flex-end;
    left: 32px; right: 41px;
    height: 22px;
  }
  .field__label { white-space: nowrap; line-height: 16px; }
  .field__line { border-bottom: 1px solid var(--rule); height: 100%; margin: 0 3px 0 3px; }
  .field--name { top: 39px; }
  .field--name .field__line { flex: 1; margin-right: 0; }
  .field--when { top: 81px; }
  .field__line--date { width: 261px; }
  .field__line--time { width: 115px; }
  .field__label--time { margin-left: 4px; }
  .field__label--ampm { margin-left: 2px; }
  .write-line {
    position: absolute;
    left: 35px; right: 41px;
    border-top: 1px solid var(--rule);
  }
</style>
</head>
<body>

<section class="card card--front" aria-label="Business card front">
  <div class="name-band">
    <div class="name-band__name">DANIEL REYES</div>
    <div class="name-band__title">CEO/FOUNDER</div>
  </div>
  <div class="brand">
    <span class="brand__dot"></span>
    <span class="brand__name">The Harbourview<br>Motion Clinic</span>
  </div>

  <ul class="contact-list">
    <li>
      <svg viewBox="0 0 16 16" aria-hidden="true"><path fill="var(--brand-blue)" d="M3.6 1.2l2.2 2.9c.3.4.3.9 0 1.3L4.8 6.6c.9 1.9 2.5 3.5 4.4 4.4l1.2-1c.4-.3.9-.3 1.3 0l2.9 2.2c.4.3.5.9.1 1.3l-1.2 1.3c-.6.6-1.5.8-2.3.5C6.4 13.5 2.5 9.6.7 4.8.4 4 .6 3.1 1.2 2.5L2.3 1.1c.4-.4 1-.3 1.3.1z"/></svg>
      689 555 0142
    </li>
    <li>
      <svg viewBox="0 0 16 16" aria-hidden="true"><rect x="1" y="3" width="14" height="10" fill="var(--brand-blue)"/><path d="M1.5 3.5L8 8.5l6.5-5" fill="none" stroke="#fff" stroke-width="1.4"/></svg>
      daniel@harbourviewmotion.com
    </li>
    <li><span class="social-square"></span>/harbourviewmotion</li>
    <li><span class="social-square"></span>@harbourviewmotion</li>
  </ul>

  <address class="address">
    412 Seacliff Road<br>
    Northport, Alaska 34512<br>
    www.harbourviewmotion.com
  </address>
</section>

<section class="card card--back" aria-label="Business card back">
  <div class="watermark"></div>
  <div class="appointment">
    <div class="field field--name">
      <span class="field__label">Name</span>
      <span class="field__line"></span>
    </div>
    <div class="field field--when">
      <span class="field__label">Date</span>
      <span class="field__line field__line--date"></span>
      <span class="field__label field__label--time">Time</span>
      <span class="field__line field__line--time"></span>
      <span class="field__label field__label--ampm">am/pm</span>
    </div>
    <div class="write-line" style="top:139px"></div>
    <div class="write-line" style="top:179px"></div>
    <div class="write-line" style="top:219px"></div>
    <div class="write-line" style="top:259px"></div>
    <div class="write-line" style="top:299px"></div>
  </div>
</section>

</body>
</html>
```